Business card for law firm

Need business card for new law firm. Think confident, authoritative, conservative, but not stuffy or old-fashioned.

Contact Information for Business Card

Content for card - logo (uploaded), plus the following:

Paul Whitcombe (larger font)
Managing Partner (larger font, but not as large as name)
Level 9, 7 Ferris Lane
Sydney NSW 2000
Main Tel 02 9364 2710
Direct Tel 02 8472 3159
Email paul@qvlegal.com.au
www.qvlegal.com.au

Letterhead design should include logo plus:
Level 9, 7 Ferris Lane
Sydney NSW 2000
Tel 02 8472 3159
www.qvlegal.com.au

```html
<!DOCTYPE html>
<html lang="en">
<head>
<meta charset="utf-8">
<title>Quayvale Lawyers – Business Card</title>
<link href="https://fonts.googleapis.com/css2?family=Open+Sans:wght@400;700&display=swap" rel="stylesheet">
<style>
  :root {
    --navy: #14296b;
    --ink: #111111;
    --text: #3a3a3a;
    --rule: #c9c9c9;
    --paper: #ffffff;
    --backdrop: #e6e3df;
  }
  * { box-sizing: border-box; margin: 0; padding: 0; }
  html, body { width: 1200px; height: 997px; overflow: hidden; }
  body {
    background: var(--backdrop);
    display: flex;
    align-items: center;
    justify-content: center;
    gap: 40px;
    font-family: "Open Sans", Arial, sans-serif;
  }
  .card {
    position: relative;
    width: 540px;
    height: 309px;
    background: var(--paper);
    box-shadow: 0 6px 18px rgba(0,0,0,0.12);
    overflow: hidden;
  }

  /* neutral wordmark: one font, one weight, one colour, plain square beside */
  .brand {
    display: flex;
    align-items: center;
    gap: 10px;
    font-family: "Open Sans", Arial, sans-serif;
    font-weight: 400;
    color: var(--ink);
    white-space: nowrap;
  }
  .brand-square {
    width: 22px;
    height: 22px;
    background: var(--navy);
    flex: none;
  }
  .brand-name { font-size: 20px; line-height: 1; }

  /* contact side */
  .card-contact .brand {
    position: absolute;
    left: 28px;
    top: 88px;
    width: 220px;
    justify-content: center;
  }
  .divider {
    position: absolute;
    left: 262px;
    top: 24px;
    width: 1px;
    height: 150px;
    background: var(--rule);
  }
  .details {
    position: absolute;
    left: 282px;
    top: 24px;
    font-size: 11.5px;
    line-height: 1.4;
    color: var(--text);
  }
  .person-name {
    font-size: 14px;
    font-weight: 700;
    color: var(--navy);
    text-transform: uppercase;
    letter-spacing: 0.3px;
  }
  .person-role { font-size: 12.5px; margin-bottom: 8px; }
  .address { margin-bottom: 8px; }
  .contact-list { list-style: none; }
  .contact-list li { display: flex; align-items: center; gap: 6px; }
  .contact-list svg { width: 10px; height: 10px; flex: none; }
  .swoosh { position: absolute; left: 0; bottom: 0; width: 540px; height: 120px; }

  /* logo side */
  .card-logo { display: flex; align-items: center; justify-content: center; }
  .card-logo .brand { gap: 14px; }
  .card-logo .brand-square { width: 32px; height: 32px; }
  .card-logo .brand-name { font-size: 30px; }
</style>
</head>
<body>
  <section class="card card-contact">
    <div class="brand">
      <div class="brand-square"></div>
      <div class="brand-name">Quayvale Lawyers</div>
    </div>
    <div class="divider"></div>
    <div class="details">
      <p class="person-name">Paul Whitcombe</p>
      <p class="person-role">Managing Partner</p>
      <p class="address">Level 9, 7 Ferris Lane<br>Sydney NSW 2000</p>
      <ul class="contact-list">
        <li><svg viewBox="0 0 10 10"><path d="M2 1 L4 1 L4.6 3 L3.4 3.8 Q4.4 5.8 6.2 6.6 L7 5.4 L9 6 L9 8 Q5 9.2 2 6 Q0.6 3.6 2 1 Z" fill="var(--navy)"/></svg>02 9364 2710 (Main)</li>
        <li><svg viewBox="0 0 10 10"><path d="M2 1 L4 1 L4.6 3 L3.4 3.8 Q4.4 5.8 6.2 6.6 L7 5.4 L9 6 L9 8 Q5 9.2 2 6 Q0.6 3.6 2 1 Z" fill="var(--navy)"/></svg>02 8472 3159 (Direct)</li>
        <li><svg viewBox="0 0 10 10"><circle cx="5" cy="5" r="5" fill="var(--navy)"/><rect x="2.5" y="3.3" width="5" height="3.4" fill="none" stroke="#fff" stroke-width="0.7"/><path d="M2.5 3.3 L5 5.2 L7.5 3.3" fill="none" stroke="#fff" stroke-width="0.7"/></svg>paul@qvlegal.com.au</li>
        <li><svg viewBox="0 0 10 10"><circle cx="5" cy="5" r="5" fill="var(--navy)"/><circle cx="5" cy="5" r="3.2" fill="none" stroke="#fff" stroke-width="0.6"/><ellipse cx="5" cy="5" rx="1.4" ry="3.2" fill="none" stroke="#fff" stroke-width="0.6"/><path d="M1.8 5 H8.2" stroke="#fff" stroke-width="0.6"/></svg>www.qvlegal.com.au</li>
      </ul>
    </div>
    <svg class="swoosh" viewBox="0 0 540 120" preserveAspectRatio="none" aria-hidden="true">
      <path d="M0 120 Q240 20 540 16 L540 22 Q250 28 0 120 Z" fill="var(--ink)"/>
      <path d="M0 120 Q250 30 540 22 L540 120 Z" fill="var(--navy)"/>
    </svg>
  </section>

  <section class="card card-logo">
    <div class="brand">
      <div class="brand-square"></div>
      <div class="brand-name">Quayvale Lawyers</div>
    </div>
  </section>
</body>
</html>
```